Business card for a Exhibition booth fabrication company

Hi. My company would like to change our corporate name card. We are an events and Exhibition stand builder company. We would like our corporate name card to resonate what we do. I need someone to create something unique that relates to the industry that I am in. The graphic designer should be creative to incorporate the elements of my industry and try to blend in well in the design of the card. Our aim is to ensure that we are unique and our card can look different from our competitors.
Updates

Target Market(s)

Marketing and events manager from all companies

Contact Information for Business Card

The business card should have the following details:
Name
Job Title
Email
Website

Colors

Designer to choose colors to be used in the design.

Requirements
Must have
• The card must be look something that is relevant to the service that I am providing. My website is: www.velmora-buildworks.com
• You can see my website to get more information on what service that I am doing
Nice to have
• On the back of my card, I would like to have a globe image with the incorporation of my company logo. This is to indicate that my services can be done in any part of the world.

```html
<!DOCTYPE html>
<html lang="en">
<head>
<meta charset="utf-8">
<title>Velmora Buildworks – Business Card</title>
<link href="https://fonts.googleapis.com/css2?family=Open+Sans:wght@400;600;700&display=swap" rel="stylesheet">
<style>
  :root {
    --bg: #e9e9eb;
    --card: #ffffff;
    --brand-red: #e8202a;
    --brand-grey: #6b6b6d;
    --soft-grey: #9c9c9e;
    --map-light: #f1f1f1;
    --map-dark: #c4c4c6;
    --white: #ffffff;
  }
  * { box-sizing: border-box; margin: 0; padding: 0; }
  html, body { width: 1200px; height: 960px; overflow: hidden; }
  body {
    background: var(--bg);
    font-family: "Open Sans", Arial, sans-serif;
    position: relative;
  }
  .card {
    position: absolute;
    left: 250px;
    width: 700px;
    height: 400px;
    background: var(--card);
    box-shadow: 0 6px 18px rgba(0,0,0,0.12);
    overflow: hidden;
  }
  .card-back { top: 50px; }
  .card-front { top: 510px; }

  /* Back */
  .world-area {
    position: absolute;
    left: 150px; top: 30px;
    width: 500px; height: 270px;
    border-radius: 50% 50% 45% 45%;
    background: radial-gradient(ellipse at 55% 45%, var(--map-dark) 0%, #d8d8da 45%, var(--map-light) 80%, rgba(255,255,255,0) 100%);
  }
  .back-brand {
    position: absolute;
    left: 0; right: 0; top: 240px;
    display: flex; align-items: center; justify-content: center; gap: 14px;
  }
  .brand-dot {
    width: 26px; height: 26px; border-radius: 50%;
    background: var(--brand-red);
  }
  .brand-name {
    font-weight: 600;
    color: var(--brand-grey);
    letter-spacing: 3px;
    text-transform: uppercase;
  }
  .back-brand .brand-name { font-size: 30px; }

  /* Front */
  .front-brand {
    position: absolute;
    left: 40px; top: 48px;
    display: flex; align-items: center; gap: 12px;
  }
  .front-brand .brand-name { font-size: 24px; }
  .front-brand .brand-dot { width: 20px; height: 20px; }
  .person {
    position: absolute;
    left: 40px; top: 112px;
  }
  .person-name {
    font-weight: 700; color: var(--brand-red);
    font-size: 21px; letter-spacing: 0.5px;
  }
  .person-title {
    color: var(--brand-grey); font-size: 15px; letter-spacing: 0.5px;
  }
  .wave { position: absolute; left: 0; top: 0; }
  .contacts {
    position: absolute;
    right: 34px; top: 250px;
    list-style: none;
    color: var(--white);
    font-size: 17px;
    text-align: right;
  }
  .contacts li {
    display: flex; justify-content: flex-end; align-items: center; gap: 10px;
    height: 30px;
  }
  .contacts .icon { width: 18px; height: 18px; flex: none; }
  .contacts .no-icon { margin-right: 28px; }
</style>
</head>
<body>

<section class="card card-back" aria-label="Card back">
  <div class="world-area" role="img" aria-label="Faded grey world map"></div>
  <div class="back-brand">
    <span class="brand-dot"></span>
    <span class="brand-name">Velmora Buildworks</span>
  </div>
</section>

<section class="card card-front" aria-label="Card front">
  <svg class="wave" width="700" height="400" viewBox="0 0 700 400" aria-hidden="true">
    <path d="M0 160 C130 200 260 225 420 222 C540 220 630 210 700 214 L700 236 C620 232 540 240 420 246 C260 252 120 230 0 190 Z" fill="var(--soft-grey)"/>
    <path d="M0 196 C140 240 280 262 440 252 C560 244 640 238 700 244 L700 400 L0 400 Z" fill="var(--brand-red)"/>
    <path d="M60 220 C200 262 330 270 460 258 C560 250 630 246 700 250" fill="none" stroke="var(--white)" stroke-width="2.5"/>
  </svg>

  <div class="front-brand">
    <span class="brand-dot"></span>
    <span class="brand-name">Velmora Buildworks</span>
  </div>

  <div class="person">
    <p class="person-name">DANIEL ORWELL</p>
    <p class="person-title">PRESIDENT</p>
  </div>

  <ul class="contacts">
    <li>012-555-0148
      <svg class="icon" viewBox="0 0 24 24" aria-hidden="true"><path fill="#fff" d="M6.6 10.8a15 15 0 0 0 6.6 6.6l2.2-2.2a1 1 0 0 1 1-.25 11.4 11.4 0 0 0 3.6.57 1 1 0 0 1 1 1V20a1 1 0 0 1-1 1A17 17 0 0 1 3 4a1 1 0 0 1 1-1h3.5a1 1 0 0 1 1 1c0 1.25.2 2.45.57 3.57a1 1 0 0 1-.25 1z"/></svg>
    </li>
    <li>info@velmora-buildworks.com
      <svg class="icon" viewBox="0 0 24 24" aria-hidden="true"><rect x="2" y="5" width="20" height="14" fill="none" stroke="#fff" stroke-width="2"/><path d="M2 5l10 8 10-8" fill="none" stroke="#fff" stroke-width="2"/></svg>
    </li>
    <li>www.velmora-buildworks.com
      <svg class="icon" viewBox="0 0 24 24" aria-hidden="true"><circle cx="12" cy="12" r="9" fill="none" stroke="#fff" stroke-width="2"/><ellipse cx="12" cy="12" rx="4" ry="9" fill="none" stroke="#fff" stroke-width="1.6"/><path d="M3 12h18" stroke="#fff" stroke-width="1.6"/></svg>
    </li>
    <li class="no-icon">Street Name, City Name, Zipcode - 01234</li>
  </ul>
</section>

</body>
</html>
```